Online training business needs new website

We need a new wordpress website as a result of a rebranding. The business is a crisis management training company focussed on online training and simulation exercises. We only need a 4 page site - home, about us, contact us and blog. However we must be able to add additional tabs in the header to redirect to our sales and marketing system (Kartra). As these change from time to time, we must be able to add and delete as required.The site must be editable by us, with a basic understanding of wordpress and no understanding of coding. We don't want to have to employ someone to change text, add posts or add a new workshops etc. The theme chosen must be easy to edit by a beginner.

Target Market(s)

Senior managers food and consumer goods companies

Industry/Entity Type

Consulting

Coding

Coded - Design and coding required

Font styles to use
Sans Serif

Requirements
Must have
• Home page, about us, contact us, blog
• Colour scheme from logo (attached) - maroon, blue and grey
• If you go to the current website "tidewellcollege.com" and click on the "workshops" tab you will see the content I need on the home page for the plumvantage.com site
Nice to have
• Modern, simple and minimalist design is preferred

```html
<!DOCTYPE html>
<html lang="en">
<head>
<meta charset="utf-8">
<title>Plum Vantage – Crisis Management Training</title>
<link href="https://fonts.googleapis.com/css2?family=Roboto:wght@400;500;700&family=Roboto+Condensed:wght@400;700&display=swap" rel="stylesheet">
<style>
:root{
  --maroon:#7a1040;
  --maroon-dark:#5e0b31;
  --navy:#0f3a73;
  --navy-dark:#0b2c59;
  --ink:#1d1d1d;
  --text:#555;
  --grey:#e9e9ee;
  --white:#fff;
  --footer:#0e0e14;
  --footer-bar:#0a0a0f;
  --gold:#f4b400;
}
*{box-sizing:border-box;margin:0;padding:0}
html,body{width:1200px;height:4478px;overflow:hidden}
body{position:relative;background:var(--white);font-family:"Roboto",sans-serif;color:var(--ink)}
.abs{position:absolute}
.cond{font-family:"Roboto Condensed",sans-serif}

/* header */
.topline{left:0;top:0;width:1200px;height:5px;background:var(--navy)}
.header{left:0;top:5px;width:1200px;height:145px;background:var(--white)}
.brand{left:90px;top:40px;display:flex;align-items:center;gap:12px}
.brand-dot{width:44px;height:44px;border-radius:50%;background:var(--maroon)}
.brand-name{font-size:28px;font-weight:700;color:var(--navy);line-height:1}
.nav{left:290px;top:68px;display:flex;gap:38px;font-size:17px;font-weight:500}
.nav a{color:var(--ink);text-decoration:none}
.nav a.active{color:var(--maroon)}
.phone{left:728px;top:66px;display:flex;align-items:center;gap:8px;font-size:19px;font-weight:500}
.search{left:905px;top:60px;width:200px;height:38px;border:2px solid #cfcfcf;border-radius:20px;padding:0 14px;display:flex;align-items:center;justify-content:space-between;font-size:14px;color:#777}

/* hero */
.hero{left:0;top:150px;width:1200px;height:585px;background:linear-gradient(100deg,#0d1520 0%,#1c2533 45%,#3a3f47 70%,#1a1e26 100%)}
.hero-brand{left:90px;top:150px;display:flex;align-items:center;gap:18px}
.hero-dot{width:70px;height:70px;border-radius:50%;background:var(--maroon)}
.hero-title{font-size:92px;font-weight:400;color:var(--white);line-height:1}
.hero-sub{left:90px;top:270px;width:560px;font-size:28px;line-height:44px;color:var(--white)}
.hero-arrows{left:92px;top:460px;display:flex;gap:22px;color:var(--white);font-size:26px}

/* about */
.about-frame{left:93px;top:833px;width:325px;height:407px;border:3px solid var(--maroon)}
.about-photo{left:113px;top:853px;width:375px;height:367px;background:linear-gradient(135deg,#5d7a9a,#9fb5c9 50%,#3d4c5f)}
.about-card{left:488px;top:853px;width:612px;height:367px;background:var(--white);box-shadow:0 4px 18px rgba(0,0,0,.18);padding:30px 40px}
.section-title{display:flex;align-items:center;gap:12px}
.mini-ring{width:40px;height:40px;border-radius:50%;border:5px solid var(--maroon)}
.about-card h2{font-size:44px;font-weight:400;color:var(--maroon)}
.about-card p{margin-top:14px;font-size:15px;line-height:29px;color:var(--text)}
.btn{display:inline-block;border-radius:20px;font-size:14px;font-weight:500;text-align:center}
.btn-navy{background:var(--navy);color:var(--white);padding:9px 22px;margin-top:12px}

/* steps */
.steps{left:0;top:1340px;width:1200px;height:690px;background:linear-gradient(160deg,var(--maroon) 0%,var(--maroon-dark) 100%)}
.ring-white{width:44px;height:44px;border-radius:50%;border:5px solid var(--white)}
.center-ring{left:578px}
.steps h2{left:0;top:125px;width:1200px;text-align:center;font-size:38px;font-weight:400;color:var(--white)}
.step{top:295px;width:315px;height:293px;background:var(--white);text-align:center;padding-top:82px}
.step-icon{left:50%;top:-60px;width:120px;height:120px;margin-left:-60px;border-radius:50%;border:6px solid var(--white);display:flex;align-items:center;justify-content:center}
.step h3{font-size:22px;font-weight:400}
.step p{margin:14px auto 0;width:250px;font-size:15px;line-height:25px;color:var(--text)}
.btn-outline{margin-top:18px;border:2px solid #bbb;padding:6px 20px;color:var(--ink)}
.btn-maroon{margin-top:18px;background:var(--maroon);color:var(--white);padding:8px 22px}

/* training */
.training-ring{left:578px;top:2140px;border-color:var(--maroon)}
.training h2{left:0;top:2195px;width:1200px;text-align:center;font-size:42px;font-weight:400}
.course{top:2295px;width:490px;height:440px;background:var(--white);box-shadow:0 4px 16px rgba(0,0,0,.2)}
.course-img{height:255px}
.course-body{padding:22px 36px}
.course h3{font-size:26px;font-weight:400}
.course p{margin-top:12px;font-size:14px;line-height:22px;color:var(--text)}
.read-more{display:inline-block;margin-top:12px;font-size:14px;font-weight:700;color:var(--maroon);border-bottom:2px solid var(--maroon);padding-bottom:2px}

/* blog */
.blog{left:0;top:2855px;width:1200px;height:680px;background:linear-gradient(160deg,var(--navy) 0%,var(--navy-dark) 100%)}
.blog h2{left:0;top:130px;width:1200px;text-align:center;font-size:42px;font-weight:400;color:var(--white)}
.post{top:245px;width:327px}
.post-img{height:170px}
.post-card{margin:-2px 20px 0;background:var(--white);padding:14px 14px 20px;text-align:center;height:180px}
.post-date{font-size:14px;font-weight:500;color:var(--navy)}
.post-card h3{margin-top:8px;font-size:17px;font-weight:700}
.post-card p{margin:6px auto 0;width:230px;font-size:13px;line-height:20px;color:var(--text)}
.btn-sq{display:inline-block;margin-top:12px;background:var(--maroon);color:var(--white);font-size:13px;padding:6px 24px;border-radius:3px}

/* testimonial */
.quote-mark{left:152px;top:3640px;font-size:100px;font-weight:700;color:var(--maroon);line-height:.8;font-family:"Roboto",sans-serif}
.testi-title{left:155px;top:3710px;font-size:46px;font-weight:400}
.testi-text{left:155px;top:3775px;width:530px;font-size:16px;line-height:30px;color:var(--text)}
.testi-name{left:155px;top:3910px;font-size:20px;font-weight:500;color:var(--navy)}
.stars{left:155px;top:3950px;display:flex;gap:6px}
.testi-ring{left:740px;top:3675px;width:320px;height:320px;border-radius:50%;border:3px solid var(--maroon);padding:12px}
.testi-photo{width:100%;height:100%;border-radius:50%;background:linear-gradient(160deg,#dfe4ea,#8aa1bd 60%,#2c4a76)}
.slide-arrow{top:3785px;width:42px;height:42px;border-radius:50%;border:2px solid #ccc;display:flex;align-items:center;justify-content:center;color:#777;font-size:22px;background:var(--white)}

/* footer */
.foot-line{left:0;top:4088px;width:1200px;height:12px;background:var(--navy)}
.footer{left:0;top:4100px;width:1200px;height:300px;background:var(--footer);color:var(--white)}
.foot-brand{left:125px;top:110px;display:flex;align-items:center;gap:10px}
.foot-brand .brand-dot{width:36px;height:36px}
.foot-brand .brand-name{color:var(--white);font-size:24px}
.socials{left:115px;top:190px;display:flex;gap:12px}
.socials span{width:28px;height:28px;border-radius:50%;border:2px solid var(--white)}
.foot-h{font-size:22px;font-weight:500}
.links{left:345px;top:65px}
.links ul{list-style:none;margin-top:18px;font-size:13px;line-height:23px;font-weight:500}
.links li:before{content:"» "}
.contact{left:552px;top:55px}
.contact-row{display:flex;gap:14px;align-items:flex-start;margin-top:18px;font-size:13px;font-weight:500;line-height:18px}
.know{left:825px;top:55px;width:290px}
.know p{margin-top:18px;font-size:13px;line-height:20px;font-weight:500}
.know .email{margin-top:12px;height:38px;background:var(--white);color:#777;font-size:13px;padding:11px 12px}
.know .sign{display:inline-block;margin-top:14px;background:var(--maroon);font-size:14px;font-weight:500;padding:8px 20px}
.foot-bar{left:0;top:4400px;width:1200px;height:78px;background:var(--footer-bar);color:#bbb;font-size:14px;text-align:center;line-height:78px}
</style>
</head>
<body>

<div class="abs topline"></div>
<header class="abs header">
  <div class="abs brand"><span class="brand-dot"></span><span class="brand-name">Plum Vantage</span></div>
  <nav class="abs nav"><a class="active" href="#">Home</a><a href="#">About us</a><a href="#">Blog</a><a href="#">Contact us</a></nav>
  <div class="abs phone">
    <svg width="18" height="18" viewBox="0 0 24 24"><path fill="#7a1040" d="M6.6 10.8a15.1 15.1 0 0 0 6.6 6.6l2.2-2.2c.3-.3.7-.4 1-.2 1.1.4 2.3.6 3.6.6.6 0 1 .4 1 1V20c0 .6-.4 1-1 1A17 17 0 0 1 3 4c0-.6.4-1 1-1h3.5c.6 0 1 .4 1 1 0 1.3.2 2.5.6 3.6.1.3 0 .7-.2 1z"/></svg>
    (555) 014-2870
  </div>
  <div class="abs search">Search
    <svg width="16" height="16" viewBox="0 0 24 24"><circle cx="10" cy="10" r="7" fill="none" stroke="#222" stroke-width="3"/><path d="M15 15l6 6" stroke="#222" stroke-width="3"/></svg>
  </div>
</header>

<section class="abs hero" role="img" aria-label="Photo of a businessman on the phone at a laptop in a dark office">
  <div class="abs hero-brand"><span class="hero-dot"></span><span class="hero-title cond">Plum Vantage</span></div>
  <p class="abs hero-sub">Neque porro quisquam est qui dolorem ipsum quia dolor sit amet consectetur</p>
  <div class="abs hero-arrows"><span>‹</span><span>›</span></div>
</section>

<section class="about">
  <div class="abs about-frame"></div>
  <div class="abs about-photo" role="img" aria-label="Photo of a team reviewing documents at a desk"></div>
  <div class="abs about-card">
    <div class="section-title"><span class="mini-ring"></span><h2 class="cond">About us</h2></div>
    <p>It is a long established fact that a reader will be distracted by the readable content of a page when looking at its layout. The point of using Lorem Ipsum is that it has a more-or-less normal distribution of letters, as opposed to using 'Content here, content here', making it look like readable English. Many desktop publishing packages and web page editors now use Lorem Ipsum as their default model text, and a search for 'lorem ipsum' will uncover</p>
    <span class="btn btn-navy">Read More</span>
  </div>
</section>

<section class="abs steps">
  <div class="abs ring-white center-ring" style="top:90px"></div>
  <h2 class="abs cond">We prepare your team in 3 easy steps</h2>
  <div class="abs step" style="left:93px">
    <div class="abs step-icon" style="background:var(--navy)">
      <svg width="46" height="46" viewBox="0 0 24 24"><path fill="#fff" d="M6 2h13v16H7a2 2 0 0 0 0 4h12v-2H7V20h0 12V2z"/><rect x="6" y="2" width="13" height="16" rx="1" fill="#fff"/><rect x="8.5" y="5" width="8" height="1.5" fill="#0f3a73"/></svg>
    </div>
    <h3>1. Create your plan</h3>
    <p>It is a long established fact that a reader will be distracted by the readable content of a page when</p>
    <span class="btn btn-outline">Read more</span>
  </div>
  <div class="abs step" style="left:440px">
    <div class="abs step-icon" style="background:var(--maroon)">
      <svg width="50" height="46" viewBox="0 0 26 24"><rect x="2" y="3" width="22" height="14" rx="1.5" fill="none" stroke="#fff" stroke-width="2.2"/><rect x="11" y="17" width="4" height="3" fill="#fff"/><rect x="7" y="20" width="12" height="2" fill="#fff"/></svg>
    </div>
    <h3>2. Train your people</h3>
    <p>It is a long established fact that a reader will be distracted by the readable content of a page when</p>
    <span class="btn btn-maroon">Read more</span>
  </div>
  <div class="abs step" style="left:786px">
    <div class="abs step-icon" style="background:var(--navy)">
      <svg width="50" height="46" viewBox="0 0 24 24"><path fill="#fff" d="M3 9h4l9-5v16l-9-5H3z"/><path fill="#fff" d="M6 15h3l1 5H7z"/><path d="M19 8q2 4 0 8" stroke="#fff" stroke-width="2" fill="none"/></svg>
    </div>
    <h3>3. Practice your process</h3>
    <p>It is a long established fact that a reader will be distracted by the readable content of a page when</p>
    <span class="btn btn-outline">Read more</span>
  </div>
</section>

<section class="training">
  <div class="abs mini-ring training-ring"></div>
  <h2 class="abs cond">Crisis Management Training</h2>
  <article class="abs course" style="left:97px">
    <div class="course-img" role="img" aria-label="Photo of a woman at a laptop in a bright office" style="background:linear-gradient(135deg,#d9dde2,#f1f1f1 50%,#9aa3ad)"></div>
    <div class="course-body">
      <h3>Online Training</h3>
      <p>Praesent elementum elit at tellus nec ultricies sit amet porttitor mattis enim In massa libero interdum nec interdum vel blandit</p>
      <span class="read-more">READ MORE</span>
    </div>
  </article>
  <article class="abs course" style="left:608px">
    <div class="course-img" role="img" aria-label="Photo of colleagues in a group discussion" style="background:linear-gradient(135deg,#4a5a6c,#8b97a3 50%,#2e3742)"></div>
    <div class="course-body">
      <h3>Simulation Exercises</h3>
      <p>Praesent elementum elit at tellus nec ultricies sit amet porttitor mattis enim In massa libero interdum nec interdum</p>
      <span class="read-more">READ MORE</span>
    </div>
  </article>
</section>

<section class="abs blog">
  <div class="abs ring-white center-ring" style="top:70px"></div>
  <h2 class="abs cond">Latest Blog</h2>
  <article class="abs post" style="left:78px">
    <div class="post-img" role="img" aria-label="Photo of hands reviewing charts on a desk" style="background:linear-gradient(135deg,#c9ccd2,#6d7480)"></div>
    <div class="post-card"><div class="post-date">JAN 25,2019</div><h3>Dolorem ipsum quia dolor</h3><p>It has survived not only five centuries, but also the leap into electronic</p><span class="btn-sq">Read More</span></div>
  </article>
  <article class="abs post" style="left:432px">
    <div class="post-img" role="img" aria-label="Photo of a tablet showing charts" style="background:linear-gradient(135deg,#e7edf3,#9ab3cc)"></div>
    <div class="post-card"><div class="post-date">JAN 25,2019</div><h3>Dolorem ipsum quia dolor</h3><p>It has survived not only five centuries, but also the leap into electronic</p><span class="btn-sq">Read More</span></div>
  </article>
  <article class="abs post" style="left:788px">
    <div class="post-img" role="img" aria-label="Photo of a team meeting around a table" style="background:linear-gradient(135deg,#d4d7dc,#7e8793)"></div>
    <div class="post-card"><div class="post-date">JAN 25,2019</div><h3>Dolorem ipsum quia dolor</h3><p>It has survived not only five centuries, but also the leap into electronic</p><span class="btn-sq">Read More</span></div>
  </article>
</section>

<section class="testimonial">
  <div class="abs slide-arrow" style="left:55px">‹</div>
  <div class="abs quote-mark">“</div>
  <h2 class="abs testi-title cond">Testimonial</h2>
  <p class="abs testi-text">"It is a long established fact that a reader will be distracted by the readable content of a page when looking at its layout. The point of using Lorem Ipsum is that it has a more-or-less normal distribution of letters, as opposed to using 'Content here, content here', making it look like "</p>
  <div class="abs testi-name">Daniel Reyes Cloud Engineer</div>
  <div class="abs stars">
    <svg width="150" height="24" viewBox="0 0 150 24"><g fill="#f4b400"><path id="s" d="M12 1l3.3 7 7.7.9-5.7 5.2 1.6 7.6L12 17.8 5.1 21.7l1.6-7.6L1 8.9 8.7 8z"/><use href="#s" x="31"/><use href="#s" x="62"/><use href="#s" x="93"/><use href="#s" x="124"/></g></svg>
  </div>
  <div class="abs testi-ring"><div class="testi-photo" role="img" aria-label="Portrait photo of the client giving the testimonial"></div></div>
  <div class="abs slide-arrow" style="left:1090px">›</div>
</section>

<div class="abs foot-line"></div>
<footer class="abs footer">
  <div class="abs foot-brand"><span class="brand-dot"></span><span class="brand-name">Plum Vantage</span></div>
  <div class="abs socials"><span></span><span></span><span></span><span></span></div>
  <div class="abs links">
    <div class="foot-h">Links</div>
    <ul><li>Home</li><li>About us</li><li>Training</li><li>Blog</li><li>Contact</li></ul>
  </div>
  <div class="abs contact">
    <div class="foot-h">Contact Us</div>
    <div class="contact-row">
      <svg width="14" height="18" viewBox="0 0 14 20"><path fill="#fff" d="M7 0a7 7 0 0 0-7 7c0 5 7 13 7 13s7-8 7-13a7 7 0 0 0-7-7zm0 9.5A2.5 2.5 0 1 1 7 4.5a2.5 2.5 0 0 1 0 5z"/></svg>
      <span>Plum Vantage 82 Harbor Row<br>4th Floor Lakeview 20417</span>
    </div>
    <div class="contact-row">
      <svg width="14" height="14" viewBox="0 0 24 24"><path fill="#fff" d="M6.6 10.8a15.1 15.1 0 0 0 6.6 6.6l2.2-2.2c.3-.3.7-.4 1-.2 1.1.4 2.3.6 3.6.6.6 0 1 .4 1 1V20c0 .6-.4 1-1 1A17 17 0 0 1 3 4c0-.6.4-1 1-1h3.5c.6 0 1 .4 1 1 0 1.3.2 2.5.6 3.6.1.3 0 .7-.2 1z"/></svg>
      <span>555-019-2234</span>
    </div>
    <div class="contact-row">
      <svg width="14" height="12" viewBox="0 0 24 18"><rect width="24" height="18" rx="2" fill="#fff"/><path d="M1 2l11 8 11-8" stroke="#0e0e14" stroke-width="2" fill="none"/></svg>
      <span>info@plumvantage.com</span>
    </div>
  </div>
  <div class="abs know">
    <div class="foot-h">Get to Know Us</div>
    <p>Excepteur sint occaecat cupidatat non proident, sunt in culpa qui officia deserunt</p>
    <div class="email">Enter email</div>
    <span class="sign">SIGN UP</span>
  </div>
</footer>
<div class="abs foot-bar">© 2019 Company Name All right reserved</div>

</body>
</html>
```